Vorelan.com Personal Trainer/Fitness Website

I want a website to market my personal training/Outdoor Bootcamp Class services, as well as to ditribute nutrivex. I need a logo as well I included an address for the Harbor Gales 1975 logo. I'd like Vorelan in place of Harbor Gales, and in Black and white, just different enough so I can't get sued by the PBL.
https://www.pictofind.example/imgres?imgurl=http%3A%2F%2Fwww.darnell-quibury.example%2Fwp-content%2Fuploads%2F2014%2F01%2Fgales_logo4.jpg&imgrefurl=http%3A%2F%2Fwww.darnell-quibury.example%2Fpbl-logo-redesigns-harbor-gales%2F&docid=_qkwzR7TBAgXpL&tbnid=m4tpU8KdOXjnRP%3A&w=600&h=450&client=ms-android-carrier&bih=512&biw=360&ved=0ahUKEwiRtpgyp9HMAhUTwGMKHRPMBWMQMwg6KBQwFA&iact=mrc&uact=8.
It should be about 5 pages 1. home 2. about 3. Services 4. Blog/Videos and programs 5. Contact.
http://www.dorvinfitness.example.uk/ is a website I like the style of.

Target Market(s)

Seattle area

Industry/Entity Type

Fitness

Coding

Coded - Design and coding required

Number of Pages Required

4 page

Font styles to use
Serif
Sans Serif

Requirements
Must have
• A minimal look
Nice to have
• A logo similar to the 1975 Harbor Galewinds Logo, with a Small Milo Brandt ripping his shirt open(with a picture of the logo on his shirt, picture within picture) to turn into Ironjaw in the center. Skyline is black, Background and small figure white(with black logo on shirt)

```html
<!DOCTYPE html>
<html lang="en">
<head>
<meta charset="utf-8">
<title>Vorelan – Personal Training</title>
<link href="https://fonts.googleapis.com/css2?family=Roboto:wght@400;500;700&family=Roboto+Condensed:wght@500&family=Open+Sans:wght@400;600;700&family=Lato:ital@1&display=swap" rel="stylesheet">
<style>
:root{
  --green:#0e6b3a;
  --red:#e8262b;
  --ink:#1d1d1d;
  --text:#3a3a3a;
  --footer:#000;
  --footer-box:#141414;
}
*{box-sizing:border-box;margin:0;padding:0}
html,body{width:995px;height:1200px;overflow:hidden}
body{position:relative;background:#fff;font-family:"Open Sans",sans-serif;color:var(--text)}
.abs{position:absolute}
.topbar{left:0;top:0;width:995px;height:3px;background:#000}
.header{left:0;top:3px;width:995px;height:99px;background:linear-gradient(#fff,#efefef);border-bottom:1px solid #ddd}
.brand{left:117px;top:64px;display:flex;align-items:center;gap:8px;font-family:"Roboto",sans-serif;font-weight:700;font-size:29px;line-height:30px;color:var(--green)}
.brand-dot{width:20px;height:20px;border-radius:50%;background:var(--green)}
.reserve{left:609px;top:24px;width:124px;height:28px;background:var(--green);color:#fff;font:500 13px "Roboto",sans-serif;display:flex;align-items:center;justify-content:center;border-radius:2px}
.call{left:748px;top:21px;display:flex;gap:6px;align-items:center;font-family:"Roboto",sans-serif}
.call small{display:block;color:var(--green);font-size:12px;line-height:14px}
.call strong{display:block;font-weight:400;font-size:16px;line-height:19px;color:var(--ink)}
.nav{left:428px;top:78px;display:flex;align-items:center;font:500 12px "Roboto",sans-serif;color:var(--ink)}
.nav span{padding:0 16px;border-left:1px solid #bbb;line-height:16px}
.nav span:first-child{border:0;padding-left:4px}
.hero{left:0;top:103px;width:995px;height:369px;background:
  linear-gradient(180deg,rgba(236,232,226,.0) 0%,rgba(236,232,226,0) 62%,rgba(160,104,50,.85) 78%,rgba(140,88,40,.9) 100%),
  linear-gradient(90deg,#7d7a78 0%,#cbc6bf 18%,#dcd8d2 45%,#d5d1cb 70%,#c4ccc4 88%,#b9c5bb 100%)}
.hero-arrow{width:30px;height:30px;border-radius:50%;background:#111;display:flex;align-items:center;justify-content:center}
.caption{left:0;top:435px;width:995px;height:37px;background:rgba(40,40,40,.78);color:#fff;font:500 21px "Roboto",sans-serif;display:flex;align-items:center;justify-content:center}
.section-title{left:0;top:499px;width:995px;text-align:center;font:500 22px "Roboto Condensed",sans-serif;color:var(--green)}
.title-rule{top:507px;width:215px;height:10px;border-top:1px solid #ddd;border-bottom:1px solid #ddd}
.service{width:186px;text-align:center}
.ring{margin:0 auto;width:108px;height:108px;border-radius:50%;border:2px solid #e3e3e3;background:#fff;display:flex;align-items:center;justify-content:center;box-shadow:0 10px 8px -8px rgba(0,0,0,.08)}
.ring .disc{width:94px;height:94px;border-radius:50%;background:#ececec;display:flex;align-items:center;justify-content:center}
.service h3{margin-top:24px;font:500 14px/18px "Roboto",sans-serif;color:var(--green)}
.divider{left:117px;top:749px;width:762px;height:1px;background:linear-gradient(90deg,transparent,#ddd,transparent)}
.col{top:792px;width:226px}
.col h2{font:500 17px "Roboto",sans-serif;color:var(--ink);padding-bottom:4px;border-bottom:1px dashed #bbb}
.col h2 em{font-style:normal;color:var(--green)}
.about-photo{margin-top:12px;width:225px;height:103px;background:linear-gradient(100deg,#8a6a4e 0%,#d8b48c 22%,#a57c5b 45%,#4a3b33 70%,#2e2a28 100%)}
.about p{margin-top:10px;font-size:10.5px;line-height:16px;letter-spacing:.3px}
.more{font:400 10.5px "Roboto",sans-serif;color:var(--green);text-align:right;margin-top:14px;padding-right:6px}
.reviewer{margin-top:12px;display:flex;gap:10px}
.avatar{width:73px;height:73px;border-radius:50%;border:3px solid var(--red);background:#d9d9d9}
.who{margin-top:22px;font:500 12px "Roboto",sans-serif;color:var(--ink)}
.who small{font:400 10px "Open Sans",sans-serif}
.quote{margin-top:10px;border:1px solid #e5e5e5;padding:8px 10px;font:italic 11.3px/18.5px "Lato",sans-serif;color:#333}
.quote b{color:#bbb;font-size:16px}
.field{width:212px;height:23px;border:1px solid #bbb;border-radius:2px;margin-top:13px;font-size:10px;padding:5px 8px;color:#555;box-shadow:inset 0 1px 2px rgba(0,0,0,.08)}
.field.msg{height:66px}
.submit{margin-top:9px;width:56px;height:19px;background:var(--red);color:#fff;font:700 11px "Open Sans",sans-serif;display:flex;align-items:center;justify-content:center;border-radius:2px}
.footer{left:0;top:1063px;width:995px;height:137px;background:var(--footer);border-top:2px solid #666;color:#fff}
.fbox{top:24px;height:63px;background:var(--footer-box);border:1px solid #333;padding:6px 10px}
.fbox h4{font:500 12px "Roboto",sans-serif;margin-bottom:8px}
.nl{display:flex;gap:6px}
.nl span{width:150px;height:23px;background:#fff;color:#333;font-size:12px;padding:3px 7px}
.nl i{width:26px;height:23px;background:#fff;display:flex;align-items:center;justify-content:center}
.fcontact{font-size:10px;line-height:16px}
.social{display:flex;gap:9px}
.social span{width:22px;height:22px;border-radius:3px}
.fbrand{left:800px;top:34px;display:flex;align-items:center;gap:7px;font:700 20px "Roboto",sans-serif;color:#fff}
.fbrand i{width:18px;height:18px;border-radius:50%;background:var(--green)}
.flinks{top:114px;font:400 10.5px "Roboto",sans-serif}
</style>
</head>
<body>
<div class="abs topbar"></div>
<header class="abs header"></header>
<div class="abs brand"><span class="brand-dot"></span>VORELAN</div>
<div class="abs reserve">RESERVE A SEAT</div>
<div class="abs call">
  <svg width="26" height="26" viewBox="0 0 26 26"><circle cx="13" cy="13" r="11.5" fill="none" stroke="#e8262b" stroke-width="1.6"/><path d="M9 7c-1 1-1.5 3 0 6s4 5.5 6.5 6c1.2.2 2-.5 2.4-1.2l-2.3-2-1.4 1c-1.5-.7-3-2.5-3.6-4l1-1.3-1.6-2.7z" fill="#e8262b"/></svg>
  <div><small>Call Us Today</small><strong>206 555 0148</strong></div>
</div>
<nav class="abs nav">
  <span><svg width="15" height="13" viewBox="0 0 15 13"><path d="M7.5 0L0 6.5h2V13h4V9h3v4h4V6.5h2z" fill="#0e6b3a"/></svg></span>
  <span>ABOUT</span><span>SERVICES</span><span>VIDEOS</span><span>PROGRAMS</span><span>CONTACT US</span>
</nav>

<div class="abs hero" role="img" aria-label="Photo of an indoor training studio with exercise balls, a squat rack and a wooden floor"></div>
<div class="abs hero-arrow" style="left:51px;top:261px"><svg width="10" height="14"><path d="M8 1L2 7l6 6" stroke="#fff" fill="none" stroke-width="1.5"/></svg></div>
<div class="abs hero-arrow" style="left:913px;top:261px"><svg width="10" height="14"><path d="M2 1l6 6-6 6" stroke="#fff" fill="none" stroke-width="1.5"/></svg></div>
<div class="abs caption">GET FIT AND HAVE FUN THE WAY IT SHOULD BE</div>

<div class="abs title-rule" style="left:197px"></div>
<div class="abs title-rule" style="left:588px"></div>
<h2 class="abs section-title">OUR SERVICES</h2>

<div class="abs service" style="left:125px;top:554px"><div class="ring"><div class="disc">
  <svg width="58" height="30" viewBox="0 0 58 30" fill="#0e6b3a" aria-label="Dumbbell icon"><rect x="0" y="10" width="6" height="10" rx="2"/><rect x="6" y="2" width="8" height="26" rx="2"/><rect x="14" y="12" width="30" height="6"/><rect x="44" y="2" width="8" height="26" rx="2"/><rect x="52" y="10" width="6" height="10" rx="2"/></svg>
</div></div><h3>PERSONAL<br>TRAINING</h3></div>

<div class="abs service" style="left:310px;top:554px"><div class="ring"><div class="disc">
  <svg width="46" height="52" viewBox="0 0 46 52" aria-label="Stopwatch icon"><rect x="18" y="0" width="10" height="6" rx="1.5" fill="#0e6b3a"/><rect x="21" y="5" width="4" height="5" fill="#0e6b3a"/><circle cx="23" cy="31" r="19" fill="none" stroke="#0e6b3a" stroke-width="5"/><path d="M23 31V19" stroke="#0e6b3a" stroke-width="4" stroke-linecap="round"/><circle cx="23" cy="31" r="3.5" fill="#0e6b3a"/><path d="M37 12l4-4" stroke="#0e6b3a" stroke-width="4" stroke-linecap="round"/></svg>
</div></div><h3>OUTDOOR BOOTCAMP<br>CLASSES</h3></div>

<div class="abs service" style="left:497px;top:554px"><div class="ring"><div class="disc">
  <svg width="50" height="50" viewBox="0 0 50 50" aria-label="Outdoor trail icon"><path d="M2 44L18 18l9 13 6-8 15 21z" fill="#0e6b3a"/><circle cx="38" cy="10" r="6" fill="#0e6b3a"/><path d="M0 47h50" stroke="#0e6b3a" stroke-width="3"/></svg>
</div></div><h3>OUTDOOR GROUP<br>TRAINING</h3></div>

<div class="abs service" style="left:682px;top:554px"><div class="ring"><div class="disc">
  <svg width="54" height="46" viewBox="0 0 54 46" aria-label="Monitor with play button icon"><rect x="2" y="2" width="50" height="32" rx="2" fill="none" stroke="#0e6b3a" stroke-width="4"/><path d="M22 11v14l12-7z" fill="#0e6b3a"/><rect x="24" y="34" width="6" height="6" fill="#0e6b3a"/><rect x="14" y="40" width="26" height="4" rx="1" fill="#0e6b3a"/></svg>
</div></div><h3>ONLINE<br>COACHING</h3></div>

<div class="abs divider"></div>

<section class="abs col about" style="left:117px">
  <h2>ABOUT <em>VORELAN</em></h2>
  <div class="about-photo" role="img" aria-label="Photo of people running on treadmills in a gym"></div>
  <p>Lorem ipsum dolor sit amet, consectetuer adipiscing elit, sed diam nonummy nibh euismod tincidunt ut laoreet dolore magna aliquam erat volutpat.</p>
  <div class="more">READ MORE »</div>
</section>

<section class="abs col" style="left:381px;width:230px">
  <h2>CLIENT <em>REVIEWS</em></h2>
  <div class="reviewer">
    <div class="avatar" role="img" aria-label="Client portrait photo"></div>
    <div>
      <div class="who">Reid M. on <small>March 20, 2016</small></div>
      <svg width="104" height="16" viewBox="0 0 104 16" style="margin-top:6px">
        <defs><path id="st" d="M8 0l2.4 5 5.4.6-4 3.7 1.1 5.4L8 12 3.1 14.7l1.1-5.4-4-3.7 5.4-.6z"/></defs>
        <g fill="#a9a9a9"><use href="#st"/><use href="#st" x="22"/><use href="#st" x="44"/><use href="#st" x="66"/></g>
        <use href="#st" x="88" fill="#444"/>
      </svg>
    </div>
  </div>
  <div class="quote"><b>“</b> I have been training with Dorian for just a few weeks now and am already feeling a difference between this and past efforts to get healthy... <b>”</b></div>
  <div class="more">READ MORE »</div>
</section>

<section class="abs col" style="left:653px">
  <h2>QUICK <em>CONTACT</em></h2>
  <div class="field">Name</div>
  <div class="field">Email</div>
  <div class="field">Phone</div>
  <div class="field msg">Message</div>
  <div class="submit">SUBMIT</div>
</section>

<footer class="abs footer">
  <div class="abs fbox" style="left:117px;width:204px">
    <h4>SUBSCRIBE TO NEWSLETTER</h4>
    <div class="nl"><span>Email here</span><i><svg width="10" height="12"><path d="M2 1l6 5-6 5" stroke="#0e6b3a" stroke-width="2.5" fill="none"/></svg></i></div>
  </div>
  <div class="abs fbox" style="left:351px;width:118px">
    <h4>CONTACT US</h4>
    <div class="fcontact">☎ 206-555-0172<br>✉ info@vorelan.com</div>
  </div>
  <div class="abs fbox" style="left:501px;width:137px">
    <h4>FOLLOW US</h4>
    <div class="social"><span style="background:#3b5a98"></span><span style="background:#2fa5de"></span><span style="background:#1273b5"></span><span style="background:#d9453a"></span></div>
  </div>
  <div class="abs fbrand"><i></i>VORELAN</div>
  <div class="abs flinks" style="left:118px">HOME &nbsp;•&nbsp; ABOUT &nbsp;•&nbsp; SERVICES &nbsp;•&nbsp; VIDEOS &nbsp;•&nbsp; PROGRAMS &nbsp;•&nbsp; CONTACT US</div>
  <div class="abs flinks" style="left:512px">COPYRIGHT 2016 © VORELAN All Rights Reserved • Privacy Policy • Terms of Use</div>
</footer>
</body>
</html>
```